Request for Business Card Design

Hi. My name is Marlene, I am looking for a new business card design for my company, Quarrow Signal Instruments, LLC. I really like the design you did for Tarsel Venture and was hoping you could do something similar using our full logo and our mark. I am also open to any raised texture design using our mark. I have attached our full logo, which would need to be somewhere on the card, as well as the mark in both outline and full form, as well as our brand colors / guide. The card does not have to be white, as long as our logo and mark appear. I actually like darker colored business cards more, but am open to all options. If you are interested in working with me, please let me know. We would also take the business card design into letterhead design if you can do that.

```html
<!DOCTYPE html>
<html lang="en">
<head>
<meta charset="utf-8">
<title>Quarrow Signal Instruments — Business Card</title>
<link rel="stylesheet" href="https://fonts.googleapis.com/css2?family=Barlow:wght@400;500;600;700&family=Nunito:wght@800&display=swap">
<style>
  :root {
    --stage: #d9d9d9;
    --card-dark: #242223;
    --card-mid: #3a3839;
    --teal: #168db0;
    --teal-light: #4fb3d6;
    --paper: #ececec;
    --ink-light: #f2f2f2;
    --ink-soft: #dcdcdc;
  }
  * { box-sizing: border-box; margin: 0; padding: 0; }
  html, body { width: 1200px; height: 1200px; overflow: hidden; }
  body {
    background: var(--stage);
    font-family: "Barlow", sans-serif;
    position: relative;
  }
  .card {
    position: absolute;
    left: 170px;
    width: 860px;
    height: 490px;
    border-radius: 28px;
    overflow: hidden;
    background: linear-gradient(135deg, var(--card-mid) 0%, var(--card-dark) 60%);
    box-shadow: 0 6px 18px rgba(0,0,0,0.25);
  }
  .card--front { top: 70px; }
  .card--back { top: 640px; }

  /* Front */
  .brand {
    position: absolute;
    left: 150px;
    top: 178px;
    display: flex;
    align-items: center;
    gap: 34px;
  }
  .brand__dot {
    width: 120px; height: 120px;
    border-radius: 50%;
    background: var(--teal-light);
  }
  .brand__name {
    color: var(--ink-light);
    font-weight: 700;
    line-height: 1;
  }
  .brand__name-main {
    display: block;
    font-size: 84px;
    letter-spacing: 10px;
  }
  .brand__name-sub {
    display: block;
    font-size: 24px;
    letter-spacing: 1.5px;
    margin-top: 6px;
  }

  /* Back */
  .contact {
    position: absolute;
    left: 60px;
    top: 62px;
    color: var(--ink-soft);
  }
  .contact__name {
    font-family: "Nunito", sans-serif;
    font-weight: 800;
    font-size: 40px;
    color: var(--teal-light);
    line-height: 1;
  }
  .contact__role {
    font-size: 25px;
    letter-spacing: 1px;
    margin-top: 6px;
    margin-left: 14px;
  }
  .contact__address {
    font-size: 27px;
    letter-spacing: 1.2px;
    line-height: 1.22;
    margin-top: 94px;
    margin-left: 40px;
  }
  .contact__lines {
    list-style: none;
    margin-top: 22px;
    margin-left: 40px;
  }
  .contact__lines li {
    display: flex;
    align-items: center;
    gap: 14px;
    font-size: 27px;
    letter-spacing: 1.2px;
    line-height: 1.2;
  }
  .contact__icon { width: 20px; height: 20px; flex: none; fill: var(--teal-light); }

  .corner-panel {
    position: absolute;
    right: 0; top: 0;
    width: 330px; height: 490px;
    background: var(--paper);
    border-radius: 0 0 0 60px;
  }
  .mark-field {
    position: absolute;
    right: 40px;
    top: 70px;
    width: 380px; height: 380px;
    border-radius: 50%;
    background: var(--teal);
    border: 14px solid var(--paper);
  }
</style>
</head>
<body>

<section class="card card--front" aria-label="Business card front">
  <div class="brand">
    <span class="brand__dot" aria-hidden="true"></span>
    <p class="brand__name">
      <span class="brand__name-main">QUARROW</span>
      <span class="brand__name-sub">SIGNAL INSTRUMENTS</span>
    </p>
  </div>
</section>

<section class="card card--back" aria-label="Business card back">
  <div class="corner-panel" aria-hidden="true"></div>
  <div class="mark-field" role="img" aria-label="Large brand mark area"></div>

  <div class="contact">
    <h1 class="contact__name">Marlene</h1>
    <p class="contact__role">Founder &amp; Director</p>
    <p class="contact__address">1180 Harrow Field Road.<br>Aldermoor, CO 80611</p>
    <ul class="contact__lines">
      <li>
        <svg class="contact__icon" viewBox="0 0 20 20" aria-hidden="true"><path d="M4 2l3 0 1.5 4-2 1.5c1 2.2 2.8 4 5 5l1.5-2 4 1.5v3c0 1-1 2-2 2C8 17 3 12 2 4c0-1 1-2 2-2z"/></svg>
        +001 555 210 4837
      </li>
      <li>
        <svg class="contact__icon" viewBox="0 0 20 20" aria-hidden="true"><path d="M5 2h10v5H5zM2 8h16v7h-3v3H5v-3H2zM7 13v3h6v-3z"/></svg>
        +001 555 210 4890
      </li>
      <li>
        <svg class="contact__icon" viewBox="0 0 20 20" aria-hidden="true"><path d="M2 4h16v12H2zM3.5 5.5L10 11l6.5-5.5z" fill-rule="evenodd"/></svg>
        info@quarrowsignal.com
      </li>
      <li>
        <svg class="contact__icon" viewBox="0 0 20 20" aria-hidden="true"><path d="M10 1a9 9 0 100 18 9 9 0 000-18zm-1 2.2V9H4.1A6 6 0 019 3.2zm2 0A6 6 0 0115.9 9H11zM4.1 11H9v5.8A6 6 0 014.1 11zm6.9 0h4.9A6 6 0 0111 16.8z"/></svg>
        www.quarrowsignal.com
      </li>
    </ul>
  </div>
</section>

</body>
</html>
```